SaaS Early tech startup business card design

Unique design for experience ecommerce platform company. the business cards will be used by executive members. conformance with color code is required.

```html
<!DOCTYPE html>
<html lang="en">
<head>
<meta charset="utf-8">
<title>lumora business card</title>
<link rel="stylesheet" href="https://fonts.googleapis.com/css2?family=Arimo:wght@400;700&display=swap">
<style>
  :root {
    --stage: #2b2b2e;
    --navy: #211f36;
    --paper: #ffffff;
    --teal: #15b29b;
    --ink: #5a5a5e;
    --rule: #7a7a7e;
  }
  * { margin: 0; padding: 0; box-sizing: border-box; }
  html, body { width: 1200px; height: 900px; overflow: hidden; }
  body {
    background: var(--stage);
    font-family: "Arimo", Arial, sans-serif;
    position: relative;
  }
  .card {
    position: absolute;
    left: 260px;
    width: 680px;
    height: 389px;
    border-radius: 26px;
  }
  .card--back { top: 46px; background: var(--navy); }
  .card--front { top: 466px; background: var(--paper); }

  .wordmark {
    position: absolute;
    left: 0; right: 0;
    display: flex;
    align-items: center;
    justify-content: center;
    gap: 14px;
    color: var(--teal);
    font-weight: 700;
    letter-spacing: -2px;
  }
  .wordmark__dot {
    width: 0.42em; height: 0.42em;
    background: var(--teal);
    border-radius: 4px;
  }
  .card--back .wordmark { top: 138px; font-size: 104px; line-height: 1; }
  .card--front .wordmark { top: 74px; font-size: 88px; line-height: 1; }

  .details {
    position: absolute;
    top: 198px;
    left: 0; right: 0;
    display: flex;
    justify-content: center;
    align-items: center;
  }
  .person { text-align: right; padding-right: 24px; }
  .person__name { color: var(--teal); font-weight: 700; font-size: 30px; line-height: 1.1; }
  .person__role { color: var(--ink); font-size: 20px; line-height: 1.2; }
  .divider { width: 2px; height: 80px; background: var(--rule); }
  .contact { list-style: none; padding-left: 24px; }
  .contact__item {
    display: flex; align-items: center; gap: 10px;
    color: var(--ink); font-size: 21px; line-height: 27px;
  }
  .contact__icon {
    width: 20px; height: 20px; border-radius: 5px;
    background: var(--teal);
    display: flex; align-items: center; justify-content: center;
    flex: none;
  }
  .address {
    position: absolute;
    top: 318px; left: 0; right: 0;
    text-align: center;
    color: var(--ink);
    font-size: 22px;
    letter-spacing: 0.5px;
  }
</style>
</head>
<body>
  <section class="card card--back">
    <div class="wordmark"><span class="wordmark__dot"></span>lumora</div>
  </section>

  <section class="card card--front">
    <div class="wordmark"><span class="wordmark__dot"></span>lumora</div>

    <div class="details">
      <div class="person">
        <p class="person__name">Daniel Hale</p>
        <p class="person__role">Manager</p>
      </div>
      <div class="divider"></div>
      <ul class="contact">
        <li class="contact__item">
          <span class="contact__icon">
            <svg width="12" height="12" viewBox="0 0 12 12"><path d="M2.5 1 L4.5 1 L5.2 3.6 L4 4.6 Q5 7 7.4 8 L8.4 6.8 L11 7.5 L11 9.5 Q11 11 9.5 11 Q1 10.5 1 2.5 Q1 1 2.5 1 Z" fill="#fff"/></svg>
          </span>
          123-555-0148
        </li>
        <li class="contact__item">
          <span class="contact__icon">
            <svg width="13" height="10" viewBox="0 0 13 10"><rect x="0.75" y="0.75" width="11.5" height="8.5" rx="1" fill="none" stroke="#fff" stroke-width="1.5"/><path d="M1 1 L6.5 5.5 L12 1" fill="none" stroke="#fff" stroke-width="1.5"/></svg>
          </span>
          hello@lumora.io
        </li>
        <li class="contact__item">
          <span class="contact__icon">
            <svg width="13" height="13" viewBox="0 0 13 13"><circle cx="6.5" cy="6.5" r="5.5" fill="none" stroke="#fff" stroke-width="1.4"/><ellipse cx="6.5" cy="6.5" rx="2.4" ry="5.5" fill="none" stroke="#fff" stroke-width="1.2"/><path d="M1 6.5 H12" stroke="#fff" stroke-width="1.2"/></svg>
          </span>
          www.lumora.io
        </li>
      </ul>
    </div>

    <p class="address">Your address, city, state, ZIP 0000</p>
  </section>
</body>
</html>
```